Bright Ledger Bookkeeping Business Cards

I need Business Cards for a new Bookkeeping Business on the Gold Coast, Australia called "Bright Ledger Bookkeeping". I do Bookkeeping & BAS's for small to medium size businesses onsite (ie I am Mobile) or in house (at my office). I also do one on one Training onsite with clients.
I am a Registered BAS Agent, Accredited Partner with Tallyo & Member of the LEDGRA Bookkeeping Circle. The Logo's I have uploaded all need to be on a white background.

Target Market(s)

Small to Medium Size Businesses

Industry/Entity Type

Business

Contact Information for Business Card

Bright Ledger Bookkeeping
Kim Farrow
PO Box 562 Marlin Reach, Qld 4388
ph 0488 615 903
email kim@kimfarrow-example.com.au

Font styles to use
Other font styles liked:
• Maybe something like Bradley Hand ITC

Requirements
Must have
• All logo's attached on white background.
• Should state that I am a Registered BAS Agent.
Nice to have
• I have a tag - "Bright Ledger - Clear Sums" if you think that works please add.
Should not have
• No brown, green or yellow please.

```html
<!DOCTYPE html>
<html lang="en">
<head>
<meta charset="utf-8">
<title>Bright Ledger Bookkeeping – Business Card</title>
<link href="https://fonts.googleapis.com/css2?family=Kalam:wght@400;700&display=swap" rel="stylesheet">
<style>
  :root {
    --page-bg: #e9ebef;
    --card-white: #ffffff;
    --card-shade: #eef0f3;
    --ink: #1b1b1f;
    --rule-blue: #2c4a8c;
    --band-blue: #3d5b98;
    --band-blue-light: #6482b8;
    --badge-white: #ffffff;
  }
  * { box-sizing: border-box; margin: 0; padding: 0; }
  html, body {
    width: 1200px;
    height: 818px;
    overflow: hidden;
    background: var(--page-bg);
  }
  body {
    display: flex;
    align-items: center;
    justify-content: center;
    font-family: "Kalam", cursive;
    color: var(--ink);
  }
  .business-card {
    position: relative;
    width: 900px;
    height: 515px;
    border-radius: 22px;
    overflow: hidden;
    background: linear-gradient(160deg, var(--card-white) 55%, var(--card-shade));
    box-shadow: 0 14px 30px rgba(20, 30, 60, 0.18);
  }
  .business-name {
    position: absolute;
    left: 60px;
    top: 48px;
    font-size: 62px;
    font-weight: 400;
    letter-spacing: 1px;
    white-space: nowrap;
  }
  .divider {
    position: absolute;
    top: 215px;
    height: 1.5px;
    background: var(--rule-blue);
  }
  .divider--left { left: 0; width: 400px; }
  .divider--right { left: 680px; right: 0; }
  .owner-name {
    position: absolute;
    left: 418px;
    top: 180px;
    font-size: 46px;
    white-space: nowrap;
  }
  .contact-list {
    position: absolute;
    left: 330px;
    top: 262px;
    list-style: none;
    font-size: 24px;
    line-height: 38px;
  }
  .contact-list li { white-space: nowrap; }
  .accent-band {
    position: absolute;
    left: 0;
    right: 0;
    bottom: 0;
    height: 92px;
    display: flex;
    align-items: center;
    justify-content: space-between;
    padding: 0 40px;
    background: linear-gradient(90deg, var(--band-blue-light), var(--band-blue) 35%, var(--band-blue));
  }
  .credential {
    color: var(--card-white);
    font-size: 26px;
    white-space: nowrap;
  }
  .partner-badges {
    display: flex;
    gap: 16px;
  }
  .partner-badge {
    display: block;
    width: 110px;
    height: 58px;
    border-radius: 8px;
    background: var(--badge-white);
  }
</style>
</head>
<body>
  <main class="business-card">
    <h1 class="business-name">Bright Ledger Bookkeeping</h1>
    <span class="divider divider--left"></span>
    <p class="owner-name">Kim Farrow</p>
    <span class="divider divider--right"></span>
    <ul class="contact-list">
      <li class="contact-phone">0488 615 903</li>
      <li class="contact-email">kim@kimfarrow-example.com.au</li>
      <li class="contact-address">PO Box 562 Marlin Reach, Qld 4388</li>
    </ul>
    <div class="accent-band">
      <p class="credential">Registered BAS Agent</p>
      <div class="partner-badges">
        <span class="partner-badge" role="img" aria-label="Registered BAS Agent badge"></span>
        <span class="partner-badge" role="img" aria-label="Tallyo accredited partner badge"></span>
        <span class="partner-badge" role="img" aria-label="LEDGRA Bookkeeping Circle member badge"></span>
      </div>
    </div>
  </main>
</body>
</html>
```